KAJU Freightways #ALLKAJU Business Cards & Letterhead

I am looking to business cards designed for our organization. We are currently undergoing a small re-branding that is taking place. Our organization is called KAJU Freightways and we are headquartered in Phoenix, AZ. We primarily provide transportation and logistics services to the Marlow Parcel Bureau who is our largest customer. I would like to see a design that incorporates name, title, contact info, website, and address (this will be different depending on the employee). I would also like to see some color on the business card using our logo colors or a variation. I would like our logo on the back of the business card with the website displayed. The final design should communicate that we are a next generation transportation operate that focuses on being driver-first, customer-centric, innovative, and sustainable.We would also like our #ALLKAJU catch phrase incorporated as well.

Target Market(s)

Transportation & Logistics

Industry/Entity Type

Trucking Company

Contact Information for Business Card

-First and Last Name
-Position Title
-Contact Phone
-Contact Email
-Physical Address

Font styles to use
Serif

Colors

Designer to choose colors to be used in the design.

Requirements
Must have
• -KAJU logo prominently displayed
• -#ALLKAJU catch phrase used
• -Some amount of color, design gradient, etc.
• -Logo on the back with website listed (https://www.kajufreightco.example)

```html
<!DOCTYPE html>
<html lang="en">
<head>
<meta charset="utf-8">
<title>KAJU Freightways Business Card</title>
<link href="https://fonts.googleapis.com/css2?family=Roboto+Serif:opsz,wght@8..144,400;8..144,600;8..144,700;8..144,900&family=Roboto+Slab:wght@700&display=swap" rel="stylesheet">
<style>
  :root {
    --stage: #e0e0de;
    --teal-deep: #003b47;
    --teal-dark: #0f4a55;
    --green: #7cc12a;
    --green-mid: #5f9a45;
    --white: #ffffff;
    --paper: #fafafa;
  }
  * { margin: 0; padding: 0; box-sizing: border-box; }
  html, body {
    width: 1200px; height: 828px; overflow: hidden;
    background: var(--stage);
    font-family: "Roboto Serif", Georgia, serif;
  }
  .card {
    position: absolute; top: 102px;
    width: 377px; height: 623px; overflow: hidden;
  }
  /* Back of card */
  .card-back { left: 194px; }
  .card-back .photo-wash {
    position: absolute; inset: 0;
    background: linear-gradient(20deg, var(--green) 0%, var(--green-mid) 40%, #3f7a5a 70%, var(--teal-dark) 100%);
  }
  .brand-ring {
    position: absolute; border-radius: 50%;
    display: flex; align-items: center; justify-content: center;
  }
  .card-back .brand-ring {
    left: 77px; top: 176px; width: 224px; height: 224px;
    border: 6px solid var(--white);
  }
  .brand-name {
    font-family: "Roboto Serif", Georgia, serif;
    font-weight: 900; letter-spacing: 1px;
  }
  .card-back .brand-name { color: var(--white); font-size: 60px; }
  .catch-phrase {
    position: absolute; left: 0; right: 0; top: 424px;
    text-align: center; color: var(--white);
    font-weight: 600; font-size: 18px; letter-spacing: 3px;
  }
  .back-url {
    position: absolute; left: 0; right: 0; top: 580px;
    text-align: center; color: var(--white);
    font-size: 14px; letter-spacing: 3.6px;
  }
  /* Front of card */
  .card-front { left: 628px; background: var(--paper); outline: 1px solid #d6d6d6; }
  .card-front .wave { position: absolute; left: 0; top: 0; }
  .card-front .brand-ring {
    left: 86px; top: 46px; width: 206px; height: 206px;
    border: 6px solid var(--green);
  }
  .card-front .brand-name { color: var(--teal-deep); font-size: 54px; }
  .contact {
    position: absolute; left: 0; right: 0; top: 342px;
    text-align: center; color: var(--white);
  }
  .person-name {
    font-family: "Roboto Slab", Georgia, serif;
    font-weight: 700; font-size: 24px; line-height: 32px;
  }
  .person-title { font-size: 15.5px; line-height: 22px; }
  .divider {
    display: flex; align-items: center; justify-content: center;
    gap: 10px; margin: 16px 0 18px;
  }
  .divider .rule { width: 56px; height: 1px; background: var(--white); }
  .divider .icons { display: flex; gap: 7px; padding: 0 8px; }
  .contact-lines { font-size: 14.5px; line-height: 23.5px; }
  .company { font-weight: 700; font-size: 14px; line-height: 23.5px; margin-top: 9px; }
  .address { font-size: 14.5px; line-height: 23.5px; }
</style>
</head>
<body>
  <section class="card card-back">
    <div class="photo-wash" role="img" aria-label="Faded photograph of a delivery truck cab under a teal-to-green gradient"></div>
    <div class="brand-ring"><span class="brand-name">KAJU</span></div>
    <p class="catch-phrase">#ALLKAJU</p>
    <p class="back-url">www.kajufreightco.example</p>
  </section>

  <section class="card card-front">
    <svg class="wave" width="377" height="623" viewBox="0 0 377 623" aria-hidden="true">
      <path d="M0 257 Q150 322 377 258 L377 623 L0 623 Z" fill="var(--green)"/>
      <path d="M0 269 Q150 328 377 263 L377 623 L0 623 Z" fill="var(--teal-deep)"/>
    </svg>
    <div class="brand-ring"><span class="brand-name">KAJU</span></div>

    <div class="contact">
      <h1 class="person-name">Dorian Kessler</h1>
      <p class="person-title">Chairman &amp; CEO</p>
      <div class="divider">
        <span class="rule"></span>
        <span class="icons">
          <svg width="14" height="12" viewBox="0 0 14 12" aria-label="phone"><path d="M1 4 Q7 -1 13 4 L11 5.5 L9.5 4 L4.5 4 L3 5.5 Z" fill="#fff"/><rect x="3" y="6" width="8" height="5" rx="1" fill="#fff"/></svg>
          <svg width="14" height="12" viewBox="0 0 14 12" aria-label="email"><rect x="1" y="2" width="12" height="8" fill="#fff"/><path d="M1 2 L7 7 L13 2 M1 10 L5.5 6 M13 10 L8.5 6" stroke="var(--teal-deep)" stroke-width="1" fill="none"/></svg>
          <svg width="14" height="12" viewBox="0 0 14 14" aria-label="website"><circle cx="7" cy="7" r="6" fill="#fff"/><path d="M1 7 H13 M7 1 V13 M2 4 H12 M2 10 H12" stroke="var(--teal-deep)" stroke-width="0.8"/><ellipse cx="7" cy="7" rx="3" ry="6" fill="none" stroke="var(--teal-deep)" stroke-width="0.8"/></svg>
        </span>
        <span class="rule"></span>
      </div>
      <p class="contact-lines">555-014-2290<br>dorian@kajufreightco.example<br>www.kajufreightco.example</p>
      <p class="company">KAJU Freightways &amp; Energy Services</p>
      <p class="address">4170 North Saguaro Ridge<br>Road Phoenix, AZ 85099</p>
    </div>
  </section>
</body>
</html>
```